Bright, Bold Sydney Tutoring Business Flyer Advertisment

Lumora is an up and coming tutoring business located on Sydney's Upper North Shore catering to school students of all ages. We need a flyer designed for notice boards and letter box drops to attract new clients. Our tutors are mostly university education students who are fresh, dedicated and passionate about their areas of teaching. The flyer should exhibit a bright, bold, modern, clean cut style which would appeal to both students and parents. I have attached our logo (the flyer could reflect this colour scheme), and a PDF which outlines the information we would like to appear on the flyer. This is not set in stone, but designed to act as an extremely loose guide for your creativity !

Target Market(s)

Affluent School Students and Parents

Industry/Entity Type

Tutoring

Requirements
Must have
• Logo, $10 offer, company description.
Nice to have
• Grabbing headlines to attract new clients, such as "Feeling overwhelmed at school?". We are looking for an eye catching, clean cut and professional design that has the colours to attract kids and the tone to attract parents.

```html
<!DOCTYPE html>
<html lang="en">
<head>
<meta charset="utf-8">
<title>Lumora Tutoring Flyer</title>
<link rel="stylesheet" href="https://fonts.googleapis.com/css2?family=Arvo:wght@700&family=Questrial&family=Roboto+Condensed:wght@400&display=swap">
<style>
  :root {
    --pink: #f29ac4;
    --pink-bright: #f07fb6;
    --pink-offer: #f5a3cb;
    --blue: #3d9ad8;
    --blue-box: #4aa0de;
    --ink: #4a4a4a;
    --paper: #ffffff;
    --backdrop: #e4e2e6;
    --photo-a: #c9a9a0;
    --photo-b: #8f8c7e;
  }
  * { box-sizing: border-box; margin: 0; padding: 0; }
  html, body { width: 1041px; height: 1200px; overflow: hidden; }
  body { background: var(--backdrop); position: relative; font-family: "Questrial", sans-serif; }

  .flyer {
    position: absolute; left: 197px; top: 187px;
    width: 669px; height: 865px;
    background: var(--paper);
    box-shadow: 0 6px 18px rgba(0,0,0,.18);
  }
  .flyer__header {
    position: absolute; left: 0; top: 0; width: 100%; height: 100px;
    background: var(--pink);
  }
  .flyer__headline {
    position: absolute; left: 173px; top: 22px;
    font-family: "Arvo", serif; font-weight: 700;
    font-size: 32px; line-height: 33px; letter-spacing: .5px;
    color: #fff; text-transform: uppercase;
  }
  .flyer__photo {
    position: absolute; left: 0; top: 105px; width: 100%; height: 376px;
    background: linear-gradient(120deg, #d9d4cc 0%, var(--photo-a) 40%, #b7c38f 70%, var(--photo-b) 100%);
  }
  .flyer__content { position: absolute; left: 173px; top: 503px; width: 458px; }
  .flyer__questions {
    font-family: "Arvo", serif; font-weight: 700;
    font-size: 14.5px; line-height: 19.5px; letter-spacing: .6px; color: var(--blue);
    text-transform: uppercase;
  }
  .flyer__description {
    margin-top: 2px;
    font-size: 14.6px; line-height: 17.5px; letter-spacing: .35px; color: var(--ink);
    text-align: justify;
  }
  .flyer__cta {
    margin-top: 6px;
    font-size: 14.6px; line-height: 15.5px; color: var(--blue);
    text-transform: uppercase;
  }
  .offer {
    margin-top: 7px; margin-left: 1px; width: 451px; height: 53px;
    background: var(--blue-box); padding: 4px 0 0 8px;
    font-family: "Roboto Condensed", sans-serif;
    text-transform: uppercase; font-size: 24.5px; line-height: 21.5px;
    white-space: nowrap; overflow: hidden;
  }
  .offer__lead { color: #fff; }
  .offer__price { color: var(--pink-offer); }

  .contacts { position: absolute; left: 173px; top: 775px; list-style: none; }
  .contacts li {
    display: flex; align-items: center; height: 22px;
    font-size: 15px; color: var(--blue);
  }
  .contacts svg { width: 13px; height: 13px; margin-right: 8px; flex: none; }

  .brand {
    position: absolute; left: 33px; top: 722px; width: 120px;
    text-align: center;
  }
  .brand__dot {
    display: block; width: 58px; height: 58px; margin: 0 auto 10px;
    border-radius: 50%; background: var(--blue);
  }
  .brand__name {
    font-family: "Questrial", sans-serif; font-size: 30px; line-height: 30px;
    color: #333;
  }
</style>
</head>
<body>
  <main class="flyer">
    <header class="flyer__header">
      <h1 class="flyer__headline">Feeling overwhelmed<br>by the HSC?</h1>
    </header>

    <div class="flyer__photo" role="img" aria-label="Photo of a smiling tutor helping a happy student at a laptop"></div>

    <section class="flyer__content">
      <p class="flyer__questions">Looking to improve your skills,confidence and organisation?<br>Want to increase your child’s engagement at school?</p>
      <p class="flyer__description">Lumora Tutoring offers one-on-one, individualised learning experiences to maximise academic development. Our tutors are hand selected on the basis of their qualifications, expertise and passion for inspiring young learners.</p>
      <p class="flyer__cta">Contact us today to discuss how we can help make your learning goals a reality!</p>
      <div class="offer">
        <div class="offer__lead">Mention this advertisement to claim</div>
        <div class="offer__price">Your trial session for just $10!</div>
      </div>
    </section>

    <div class="brand">
      <span class="brand__dot"></span>
      <span class="brand__name">lumora</span>
    </div>

    <ul class="contacts">
      <li>
        <svg viewBox="0 0 13 13"><rect width="13" height="13" rx="2" fill="var(--pink-bright)"/><rect x="2.5" y="3.5" width="8" height="6" fill="none" stroke="#fff" stroke-width="1.2"/><path d="M2.5 3.5 6.5 7 10.5 3.5" fill="none" stroke="#fff" stroke-width="1.2"/></svg>
        info@lumoratutoring.com.au
      </li>
      <li>
        <svg viewBox="0 0 13 13"><rect width="13" height="13" rx="2" fill="var(--pink-bright)"/><circle cx="6.5" cy="6.5" r="4" fill="none" stroke="#fff" stroke-width="1.1"/><path d="M2.5 6.5h8M6.5 2.5c-2 2.5-2 5.5 0 8M6.5 2.5c2 2.5 2 5.5 0 8" fill="none" stroke="#fff" stroke-width="1"/></svg>
        www.lumoratutoring.com.au
      </li>
      <li>
        <svg viewBox="0 0 13 13"><rect width="13" height="13" rx="2" fill="var(--pink-bright)"/><path d="M6.5 11 3.6 6.6A3.3 3.3 0 1 1 9.4 6.6Z" fill="#fff"/><circle cx="6.5" cy="5" r="1.2" fill="var(--pink-bright)"/></svg>
        Suite 12, 480 Harbourview Road Pymble, NSW 2073
      </li>
    </ul>
  </main>
</body>
</html>
```